- Redesign our business card
- Logo remains unchanged
- Current business card attached

Target Market(s)

We are a property management company

Industry/Entity Type

Business

```html
<!DOCTYPE html>
<html lang="en">
<head>
<meta charset="utf-8">
<title>Harcourt Property Group – Business Card</title>
<link rel="stylesheet" href="https://fonts.googleapis.com/css2?family=Barlow+Semi+Condensed:wght@400;600&family=Barlow:wght@400;600&display=swap">
<style>
  :root {
    --stage: #000000;
    --paper: #ffffff;
    --olive: #7b773c;
    --sand: #ddd0a8;
    --ink-strong: #6a6a6d;
    --ink-soft: #8a8a8d;
    --on-olive: #ffffff;
  }
  * { box-sizing: border-box; margin: 0; padding: 0; }
  html, body {
    width: 1200px; height: 900px; overflow: hidden;
    background: var(--stage);
  }
  .stage { position: relative; width: 1200px; height: 900px; }

  .card {
    position: absolute;
    left: 244px;
    width: 664px;
    border-radius: 18px;
    overflow: hidden;
  }

  /* Front */
  .card--front { top: 44px; height: 380px; background: var(--paper); }
  .holder { position: absolute; left: 38px; top: 42px; font-family: "Barlow Semi Condensed", sans-serif; }
  .holder__name { font-weight: 600; font-size: 21px; color: var(--ink-strong); letter-spacing: 0.02em; line-height: 1.1; }
  .holder__role { font-weight: 400; font-size: 18px; color: var(--ink-soft); margin-top: 2px; }

  .contact {
    position: absolute; right: 40px; top: 42px; width: 300px;
    text-align: right; font-family: "Barlow Semi Condensed", sans-serif;
    font-size: 16px; line-height: 24px; color: var(--ink-soft);
  }
  .contact__address { font-weight: 600; color: var(--ink-strong); letter-spacing: 0.02em; }

  .brand { position: absolute; display: flex; align-items: center; font-family: "Barlow", sans-serif; }
  .brand__square { display: block; flex: none; background: var(--sand); }
  .brand__name { font-weight: 600; letter-spacing: 0.03em; line-height: 1.1; }
  .brand__tagline { font-weight: 400; letter-spacing: 0.06em; line-height: 1.2; }

  .card--front .brand { left: 178px; top: 300px; gap: 14px; color: var(--olive); }
  .card--front .brand__square { width: 36px; height: 36px; }
  .card--front .brand__name { font-size: 16px; }
  .card--front .brand__tagline { font-size: 12px; }

  .services-band {
    position: absolute; left: 0; bottom: 0; width: 100%; height: 32px;
    background: var(--olive);
    font-family: "Barlow", sans-serif; font-size: 12px; color: var(--on-olive);
    display: flex; align-items: center; padding-left: 228px; letter-spacing: 0.01em;
  }

  /* Back */
  .card--back { top: 472px; height: 376px; background: var(--olive); }
  .back-square {
    position: absolute; left: 48px; top: 52px; width: 110px; height: 110px;
    background: var(--sand);
  }
  .card--back .brand { left: 48px; top: 170px; color: var(--on-olive); }
  .card--back .brand__name { font-size: 22px; }
  .card--back .brand__tagline { font-size: 14px; margin-top: 2px; }
  .web { position: absolute; left: 88px; top: 340px; font-family: "Barlow", sans-serif; font-size: 15px; color: var(--on-olive); letter-spacing: 0.02em; }
</style>
</head>
<body>
<main class="stage">
  <section class="card card--front" aria-label="Business card front">
    <div class="holder">
      <p class="holder__name">DANIEL HARCOURT</p>
      <p class="holder__role">Licensed Strata Manager</p>
    </div>
    <div class="contact">
      <p class="contact__address">PO BOX 48, FERNLEIGH HILLS NSW<br>2031 12/6-20 MARLOW STREET<br>EASTWOOD NSW 2045</p>
      <p>T: 02 9345 0712</p>
      <p>F: 02 9345 0718</p>
      <p>M: 0412 678 903</p>
      <p>E: info@harcourtproperty.com.au</p>
      <p>www.harcourtproperty.com.au</p>
    </div>
    <div class="brand">
      <span class="brand__square" aria-hidden="true"></span>
      <div>
        <p class="brand__name">HARCOURT PROPERTY GROUP</p>
        <p class="brand__tagline">STRATA MANAGEMENT SERVICES</p>
      </div>
    </div>
    <p class="services-band">Strata Management&nbsp;|&nbsp;Community Management&nbsp;|&nbsp;Property Management</p>
  </section>

  <section class="card card--back" aria-label="Business card back">
    <span class="back-square" aria-hidden="true"></span>
    <div class="brand">
      <div>
        <p class="brand__name">HARCOURT PROPERTY GROUP</p>
        <p class="brand__tagline">STRATA MANAGEMENT SERVICES</p>
      </div>
    </div>
    <p class="web">www.harcourtproperty.com.au</p>
  </section>
</main>
</body>
</html>
```